Business card for event manager / organizer "waiter service"

Draft of a new valuable business card for my company.
Events, personnel service providers, festivals

```html
<!DOCTYPE html>
<html lang="de">
<head>
<meta charset="utf-8">
<title>Brenners Kellnerservice – Visitenkarte</title>
<link href="https://fonts.googleapis.com/css2?family=Ubuntu:wght@300;400;700&display=swap" rel="stylesheet">
<style>
  :root {
    --backdrop: #e4e3e5;
    --paper: #ffffff;
    --tan: #b0935f;
    --ink: #1d1d1b;
    --orange: #e8731f;
    --icon-glyph: #b0935f;
  }
  * { box-sizing: border-box; margin: 0; padding: 0; }
  html, body {
    width: 1200px; height: 1200px; overflow: hidden;
    background: var(--backdrop);
    font-family: "Ubuntu", sans-serif;
  }
  .stage {
    width: 1200px; height: 1200px;
    display: flex; align-items: center; justify-content: center; gap: 70px;
  }
  .card {
    width: 460px; height: 780px;
    background: var(--paper);
    box-shadow: 0 18px 40px rgba(0,0,0,.18);
    position: relative; overflow: hidden;
  }

  /* Front */
  .card-front { display: flex; align-items: center; justify-content: center; }
  .brand { display: flex; flex-direction: column; align-items: flex-start; gap: 10px; }
  .brand-row { display: flex; align-items: center; gap: 14px; }
  .brand-mark { width: 46px; height: 46px; background: var(--orange); flex: none; }
  .brand-name {
    font-weight: 700; font-size: 30px; line-height: 1.05; color: var(--ink);
    text-transform: uppercase; letter-spacing: .5px;
  }
  .brand-tagline { font-weight: 300; font-size: 13px; color: var(--ink); padding-left: 60px; white-space: nowrap; }

  /* Back */
  .portrait-area {
    height: 360px; width: 100%;
    background: linear-gradient(180deg, #b59866 0%, #a98b57 100%);
  }
  .contact { padding: 44px 48px 0; text-align: center; color: var(--tan); }
  .holder-name { font-weight: 700; font-size: 34px; letter-spacing: .3px; }
  .holder-role { font-weight: 300; font-size: 19px; margin-top: 6px; }
  .contact-list { list-style: none; margin: 30px auto 0; display: inline-flex; flex-direction: column; gap: 9px; text-align: left; }
  .contact-item { display: flex; align-items: center; gap: 14px; font-weight: 300; font-size: 17px; }
  .contact-icon { width: 26px; height: 26px; flex: none; }
  .divider { width: 40px; height: 3px; background: var(--ink); margin: 22px auto 16px; }
  .address { font-weight: 300; font-size: 18px; }
</style>
</head>
<body>
<main class="stage">
  <section class="card card-front">
    <div class="brand">
      <div class="brand-row">
        <span class="brand-mark"></span>
        <span class="brand-name">Brenners<br>Kellnerservice</span>
      </div>
      <p class="brand-tagline">…weil jedes Fest guten Service verdient!</p>
    </div>
  </section>

  <section class="card card-back">
    <div class="portrait-area" role="img" aria-label="Porträtfoto des Inhabers in schwarzem Hemd vor sandfarbenem Hintergrund"></div>
    <div class="contact">
      <h1 class="holder-name">Jonas Brenner</h1>
      <p class="holder-role">Inhaber</p>
      <ul class="contact-list">
        <li class="contact-item">
          <svg class="contact-icon" viewBox="0 0 26 26"><circle cx="13" cy="13" r="13" fill="#1d1d1b"/><path d="M9 7.5c.8-.4 1.4 0 1.8.7l1 1.8c.3.6.1 1.1-.4 1.5l-.6.5c.6 1.4 1.6 2.5 3 3.2l.5-.6c.4-.5 1-.6 1.5-.3l1.8 1c.7.4 1 1 .6 1.8-.6 1.1-1.6 1.6-2.8 1.3-3.6-1-6.2-3.7-7.2-7.2-.3-1.2.1-2.2 1.3-2.9z" fill="var(--icon-glyph)"/></svg>
          <span>02351 472 18 30</span>
        </li>
        <li class="contact-item">
          <svg class="contact-icon" viewBox="0 0 26 26"><circle cx="13" cy="13" r="13" fill="#1d1d1b"/><rect x="9.5" y="6.5" width="7" height="13" rx="1.5" fill="var(--icon-glyph)"/><rect x="10.7" y="8.2" width="4.6" height="8" fill="#1d1d1b"/></svg>
          <span>0176 284 73 19</span>
        </li>
        <li class="contact-item">
          <svg class="contact-icon" viewBox="0 0 26 26"><circle cx="13" cy="13" r="13" fill="#1d1d1b"/><rect x="7" y="8.5" width="12" height="9" fill="var(--icon-glyph)"/><path d="M7 8.5l6 5 6-5" fill="none" stroke="#1d1d1b" stroke-width="1.2"/></svg>
          <span>info@brenners-kellnerservice.de</span>
        </li>
        <li class="contact-item">
          <svg class="contact-icon" viewBox="0 0 26 26"><circle cx="13" cy="13" r="13" fill="#1d1d1b"/><circle cx="13" cy="13" r="6" fill="none" stroke="var(--icon-glyph)" stroke-width="1.4"/><path d="M7 13h12M13 7c-2.5 3.5-2.5 8.5 0 12M13 7c2.5 3.5 2.5 8.5 0 12" fill="none" stroke="var(--icon-glyph)" stroke-width="1.2"/></svg>
          <span>www.brenners-kellnerservice.de</span>
        </li>
        <li class="contact-item">
          <svg class="contact-icon" viewBox="0 0 26 26"><circle cx="13" cy="13" r="13" fill="#1d1d1b"/></svg>
          <span>brennerskellnerservice</span>
        </li>
      </ul>
      <div class="divider"></div>
      <p class="address">Lindenweg 14, 58511 Lüdenscheid</p>
    </div>
  </section>
</main>
</body>
</html>
```